Young, dynamic furniture company needs a new business card design

We require a new business card design for our modern furniture company which supplies furniture and appliances to the property and development market.
Oakridge Interiors has become one of the leading furniture & appliance suppliers to the property market withing London. With over 10 years experience, we have increased our business to supply not only private landlords and managing agents, but also property developers, housing associations and local councils.
We offer not only a complete range of furniture which includes beds, wardrobes, dining sets and sofas, but also a high quality, full delivery and assembly service to help you with all our furnishing needs.

Target Market(s)

Private landlords, estate agents, letting agents, property management companies

Industry/Entity Type

Business

Contact Information for Business Card

Name,
Title,
Address,
Mobile,
Telephone,
Fax, Website, email address

Font styles to use
Sans Serif

Colors
3176b5
0555a3
85abd2
cfdeed

Requirements
Must have
• All the above information for each of our staff, along with our logo

```html
<!DOCTYPE html>
<html lang="en">
<head>
<meta charset="utf-8">
<title>Oakridge Interiors – Business Card</title>
<link href="https://fonts.googleapis.com/css2?family=Montserrat:wght@700&family=Roboto:wght@400;500&display=swap" rel="stylesheet">
<style>
  :root {
    --backdrop: #121a2e;
    --card-black: #000000;
    --card-white: #ffffff;
    --brand-blue: #3176b5;
    --brand-deep: #0555a3;
    --brand-navy: #1f3c7c;
    --ink: #1c1c1c;
    --ink-soft: #555555;
    --text-light: #ffffff;
  }
  * { box-sizing: border-box; margin: 0; padding: 0; }
  html, body {
    width: 1200px; height: 900px; overflow: hidden;
    background: var(--backdrop);
  }
  .canvas {
    position: relative; width: 1200px; height: 900px;
    background: radial-gradient(ellipse at center, #1a2440 0%, var(--backdrop) 70%);
  }
  .card {
    position: absolute; width: 560px; height: 320px;
    border-radius: 22px; overflow: hidden;
    box-shadow: 0 18px 40px rgba(0,0,0,.45);
  }

  /* Back of card */
  .card-back {
    left: 110px; top: 120px; background: var(--card-black);
    display: flex; flex-direction: column; align-items: center; justify-content: center;
  }
  .card-back .brand-name {
    font-family: "Roboto", sans-serif; font-weight: 500;
    font-size: 40px; color: var(--text-light); letter-spacing: 1px;
  }
  .card-back .brand-web {
    margin-top: 12px;
    font-family: "Roboto", sans-serif; font-weight: 500;
    font-size: 14px; color: var(--text-light); letter-spacing: 2px;
  }

  /* Front of card */
  .card-front { left: 530px; top: 460px; background: var(--card-black); }
  .card-front .shape { position: absolute; inset: 0; }
  .front-brand {
    position: absolute; left: 0; top: 0; width: 300px; height: 320px;
    display: flex; flex-direction: column; align-items: center; justify-content: center;
  }
  .front-brand .brand-name {
    font-family: "Roboto", sans-serif; font-weight: 500;
    font-size: 26px; color: var(--ink); letter-spacing: .5px;
  }
  .front-brand .brand-tagline {
    margin-top: 6px;
    font-family: "Roboto", sans-serif; font-weight: 400;
    font-size: 10px; color: var(--ink-soft); letter-spacing: 1.5px;
  }
  .contact {
    position: absolute; left: 340px; top: 50px; color: var(--text-light);
    font-family: "Roboto", sans-serif;
  }
  .contact .person-name {
    font-family: "Montserrat", sans-serif; font-weight: 700;
    font-size: 26px; color: var(--brand-blue); line-height: 1;
  }
  .contact .person-title {
    font-size: 12px; letter-spacing: 1px; margin-top: 4px; margin-bottom: 14px;
  }
  .contact-list { list-style: none; }
  .contact-list li {
    display: flex; align-items: center; gap: 10px;
    font-size: 12px; letter-spacing: 1px; line-height: 22px;
  }
  .contact-list svg { width: 12px; height: 12px; flex: none; fill: none; stroke: var(--brand-blue); stroke-width: 2; }
  .contact .address {
    margin-top: 14px; font-size: 12px; letter-spacing: 1px; line-height: 18px;
  }
</style>
</head>
<body>
<main class="canvas">

  <section class="card card-back" aria-label="Business card back">
    <span class="brand-name">Oakridge Interiors</span>
    <span class="brand-web">www.oakridge.co.uk</span>
  </section>

  <section class="card card-front" aria-label="Business card front">
    <svg class="shape" viewBox="0 0 560 320" aria-hidden="true">
      <path d="M0 0 H262 C352 60 362 220 330 320 H0 Z" fill="#1f3c7c"/>
      <path d="M0 0 H254 C340 60 350 220 318 320 H0 Z" fill="#3176b5"/>
      <path d="M0 0 H244 C326 60 334 220 304 320 H0 Z" fill="#ffffff"/>
    </svg>

    <div class="front-brand">
      <span class="brand-name">Oakridge Interiors</span>
      <span class="brand-tagline">TRADE FURNITURE SOLUTIONS</span>
    </div>

    <div class="contact">
      <p class="person-name">Daniel Reed</p>
      <p class="person-title">Manager</p>
      <ul class="contact-list">
        <li><svg viewBox="0 0 12 12"><path d="M2 1 L4.5 1 L5 4 L3.5 5 Q5 8 7 8.5 L8 7 L11 7.5 L11 10 Q6 11 1 2 Z"/></svg>020 7946 0321</li>
        <li><svg viewBox="0 0 12 12"><rect x="1.5" y="5" width="9" height="5.5"/><rect x="3.5" y="1.5" width="5" height="3.5"/></svg>020 7946 0388</li>
        <li><svg viewBox="0 0 12 12"><rect x="1" y="2.5" width="10" height="7"/><path d="M1 2.5 L6 6.5 L11 2.5"/></svg>daniel@oakridge.co.uk</li>
        <li><svg viewBox="0 0 12 12"><circle cx="6" cy="6" r="4.8"/><path d="M1.2 6 H10.8 M6 1.2 Q3.5 6 6 10.8 M6 1.2 Q8.5 6 6 10.8"/></svg>www.oakridge.co.uk</li>
      </ul>
      <p class="address">27 Millbrook Trade Park<br>Hornsey, London N8 4QT</p>
    </div>
  </section>

</main>
</body>
</html>
```